Renny Oskow - Free Personalised Health Consultation - "One size does not fit all"

This flyer will be left on tables/seats at speaking events and seminars and used to attain leads.

Top half will have "SMS me for a FREE Personalised Health Consultation" and my picture (see www.rennyoskow-demo.com and pick most engaging photo) and underneath my contact details. It must have lines with "Notes:" halfway down so people can take notes at the seminar and lines on the back with my contact details again and "Notes: with lines.

I am having a business card also being designed by Artvane for same and would like the flyer and business card to carry a similar feel/look for consistency.

Below is the brief for the business card being designed:
Business Card for www.rennyoskow-demo.com site. It is a trust site and I use it for 1:1 relatable connections. It is the one I use for building intimate 1:1 trust building and Exec Coaching Services and programs for high wealth individuals and corporates. I also have a commercial programmatic site of my personal health products and services and programs for main stream one to many. www.steadyforwardliving-demo.com that can also provoke thought for the www.rennyoskow-demo.com business card. (mind you will get a separate business card for that site, but want to provide context). It has a logo which you may want to draw from in designing the rennyoskow business card which is personal and is about building my brand. There is also a rennyoskow personal PX page and rennyoskow business PX page. I am a Certified Talent Compass 3.1 Coach with Norvik and you can get a corporate brief of me on there to give you more context https://www.norvikcoachhub-demo.com/coach/en-us/directory?search=renny

Target Market(s)

Exec, IT, Health conscious. Corporates wanting to run Health and Wellness programs. Those wanting to go from good to great. Millennials to Middleaged.

Industry/Entity Type

Health And Wellness

Font styles to use
Sans Serif
Other font styles liked:
• Arial and Calibri ok too

Colors

Designer to choose colors to be used in the design.

Requirements
Must have
• Picture of me - use best from www.rennyoskow-demo.com or can send one you choose.
• Contact details like my buisness card being designed by you guys in separate project.
• Name: Renny Oskow
• email: renny@rennyoskow-demo.,com
• Phone: Australia +61 400 000 137 Singapore: +65 9000 2468
Nice to have
• Open to ideas

```html
<!DOCTYPE html>
<html lang="en">
<head>
<meta charset="utf-8">
<title>Renny Oskow – Health Consultation Flyer</title>
<link rel="stylesheet" href="https://fonts.googleapis.com/css2?family=Oswald:wght@500&family=Roboto:wght@400;500;700&display=swap">
<style>
  :root {
    --page-bg: #e6e6e6;
    --paper: #ffffff;
    --ink: #1e1e1e;
    --panel-dark: #2a2a2a;
    --band-grey: #7b7b7b;
    --rule: #9a9a9a;
    --divider: #8c8c8c;
    --white: #ffffff;
  }
  * { box-sizing: border-box; margin: 0; padding: 0; }
  html, body { width: 1200px; height: 903px; overflow: hidden; }
  body {
    background: var(--page-bg);
    position: relative;
    font-family: "Roboto", Arial, sans-serif;
    color: var(--ink);
  }
  .flyer {
    position: absolute;
    top: 80px;
    width: 526px;
    height: 743px;
    background: var(--paper);
    overflow: hidden;
  }
  .flyer--front { left: 58px; }
  .flyer--back { left: 617px; }

  .hero { position: absolute; left: 0; top: 0; width: 526px; height: 429px; }
  .hero__photo {
    position: absolute; inset: 0;
    background: linear-gradient(160deg, #d9d9d9 0%, #bdbdbd 35%, #8a8a8a 60%, #c9c9c9 100%);
  }
  .hero__panel { position: absolute; left: 0; top: 0; }
  .hero__copy { position: absolute; left: 24px; top: 130px; width: 202px; color: var(--white); }
  .hero__lead {
    font-family: "Oswald", "Arial Narrow", sans-serif;
    font-weight: 500; font-size: 41px; line-height: 1; letter-spacing: -0.5px; white-space: nowrap;
  }
  .hero__free {
    font-family: "Oswald", "Arial Narrow", sans-serif;
    font-weight: 500; font-size: 114px; line-height: 0.95; margin-top: 2px; letter-spacing: 0; white-space: nowrap;
  }
  .hero__personalised { font-weight: 700; font-size: 27.5px; line-height: 1.1; margin-top: 6px; white-space: nowrap; }
  .hero__service { font-weight: 500; font-size: 18px; line-height: 1.2; margin-top: 2px; white-space: nowrap; }
  .hero__sign { font-size: 16px; text-align: right; margin-top: 12px; white-space: nowrap; }

  .notes__title { position: absolute; left: 23px; font-size: 20px; font-weight: 400; letter-spacing: 0.3px; }
  .flyer--front .notes__title { top: 442px; }
  .flyer--back .notes__title { top: 24px; }
  .notes__line { position: absolute; left: 23px; width: 478px; border-top: 1px dotted var(--rule); }

  .contact-band { position: absolute; left: 0; top: 701px; width: 526px; height: 42px; }
  .contact-band svg { position: absolute; inset: 0; }
  .contact-band__text {
    position: absolute; top: 14px; font-size: 11.5px; color: var(--white); white-space: nowrap;
  }
  .contact-band__au { left: 30px; }
  .contact-band__divider { position: absolute; left: 175px; top: 8px; width: 1px; height: 26px; background: var(--divider); }
  .contact-band__sg { left: 183px; }
  .contact-band__email { left: 348px; width: 178px; text-align: center; top: 11px; }
</style>
</head>
<body>

<section class="flyer flyer--front">
  <div class="hero">
    <div class="hero__photo" role="img" aria-label="Black and white photo of Renny Oskow in a suit, leaning on a bicycle in a colonnaded walkway"></div>
    <svg class="hero__panel" width="526" height="429" viewBox="0 0 526 429">
      <polygon points="0,28 228,28 306,228 231,429 0,429" fill="var(--panel-dark)" stroke="var(--white)" stroke-width="4"/>
    </svg>
    <div class="hero__copy">
      <p class="hero__lead">SMS me for a</p>
      <p class="hero__free">FREE</p>
      <p class="hero__personalised">PERSONALISED</p>
      <p class="hero__service">HEALTH CONSULTATION</p>
      <p class="hero__sign">- Renny Oskow</p>
    </div>
  </div>

  <h2 class="notes__title">NOTES</h2>
  <div class="notes__line" style="top:495px"></div>
  <div class="notes__line" style="top:536px"></div>
  <div class="notes__line" style="top:577px"></div>
  <div class="notes__line" style="top:617px"></div>
  <div class="notes__line" style="top:657px"></div>

  <footer class="contact-band">
    <svg width="526" height="42" viewBox="0 0 526 42">
      <rect x="0" y="0" width="526" height="42" fill="var(--band-grey)"/>
      <polygon points="0,0 348,0 333,42 0,42" fill="var(--panel-dark)"/>
    </svg>
    <span class="contact-band__text contact-band__au">Australia +61 400 000 137</span>
    <span class="contact-band__divider"></span>
    <span class="contact-band__text contact-band__sg">Singapore: +65 9000 2468</span>
    <span class="contact-band__text contact-band__email">renny@rennyoskow-demo.com</span>
  </footer>
</section>

<section class="flyer flyer--back">
  <h2 class="notes__title">NOTES</h2>
  <div class="notes__line" style="top:75px"></div>
  <div class="notes__line" style="top:116px"></div>
  <div class="notes__line" style="top:157px"></div>
  <div class="notes__line" style="top:198px"></div>
  <div class="notes__line" style="top:238px"></div>
  <div class="notes__line" style="top:278px"></div>
  <div class="notes__line" style="top:319px"></div>
  <div class="notes__line" style="top:360px"></div>
  <div class="notes__line" style="top:400px"></div>
  <div class="notes__line" style="top:441px"></div>
  <div class="notes__line" style="top:482px"></div>
  <div class="notes__line" style="top:522px"></div>
  <div class="notes__line" style="top:562px"></div>
  <div class="notes__line" style="top:603px"></div>
  <div class="notes__line" style="top:643px"></div>

  <footer class="contact-band">
    <svg width="526" height="42" viewBox="0 0 526 42">
      <rect x="0" y="0" width="526" height="42" fill="var(--band-grey)"/>
      <polygon points="0,0 348,0 333,42 0,42" fill="var(--panel-dark)"/>
    </svg>
    <span class="contact-band__text contact-band__au">Australia +61 400 000 137</span>
    <span class="contact-band__divider"></span>
    <span class="contact-band__text contact-band__sg">Singapore: +65 9000 2468</span>
    <span class="contact-band__text contact-band__email">renny@rennyoskow-demo.com</span>
  </footer>
</section>

</body>
</html>
```